Etiketten für Kosmetik Produkte  100% Natural Made in Germany
Etiketten für Kosmetik Produkte 100% Natural Made in Germany
Zielgruppe
auf Hochwertige -zertifizierte Naturprodukte wert legen.
Hergestellt in Deutschland und Verpackt
Aufgabenstellung
Hallo ihr lieben,
für die SilberTau Kosmetik - wünschen wir einen neuen frischen Style - das dunkle Etikett möchten wir los werden.
Ein helles frisches Design
Zielgruppe- alle die auf Hochwertige - zertifizierte Naturprodukte bevorzugen
Die Produkte haben mit eine VEROLT Zertifizierung - Höchste Qalität an Naturprodukte
Das Glas was wir nutzen ist ein violettes Glas und sehr hochwertig was wir beibehalten möchten.
Das Produkt ist dadurch sehr Geschütz und nachhaltig dazu
Es sind 12 Produkte - Design bleibt bei allen gleich.
Design Wunsch -!!!!
Was gut zum Glas Passt- nur kein schwarz bitte
und Produkt gut passt
Weiß - Kupfer eventuell
Kein Muss - sind für alles offen ( nur kein schwarz
Logo - Name bleibt :-)
Das Design von Tiveno Naturkosmetik
Gefällt uns sehr gut in der Richtung
Was die Natürlichkeit- Reinheit - Qualität
Verkörpert:-)
Fotos zum Prosukt:
Hier ein link zum Instagram
https://instagram.com/lurenca.sud?igshid=XkQ3bTpVmWz8Rg==
https://instagram.com/silbertau_naturkosmetik?igshid=XkQ3bTpVmWz8Rg==
An den Flyer den wir hochgeladen kann man sehen um welche Produkte es sich handelt und auch im Instagram zu sehen sind.
Wenn ihr weitere Fotos benötigen tut- bitte melden
Viel Glück :-) danke für eure Unterstützung

```html
<!DOCTYPE html>
<html lang="de">
<head>
<meta charset="utf-8">
<title>SilberTau Naturkosmetik – Etikett Lemon &amp; Orange Oil</title>
<link rel="stylesheet" href="https://fonts.googleapis.com/css2?family=Cormorant+Garamond:wght@400;500&family=Josefin+Sans:wght@300&family=Montserrat:wght@400;700&display=swap">
<style>
  :root {
    --page: #ffffff;
    --label-white: #f3f1f0;
    --ring-gold: #cfa96a;
    --brand-gold: #c9a84a;
    --ink-grey: #4a4a4a;
    --ring-text: #ffffff;
    --label-edge: #e4e1de;
  }
  html, body {
    margin: 0;
    padding: 0;
    width: 1200px;
    height: 960px;
    overflow: hidden;
    background: var(--page);
  }
  .label {
    display: block;
    width: 1200px;
    height: 960px;
  }
  .label-edge { fill: var(--label-white); stroke: var(--label-edge); stroke-width: 2; }
  .ring-band { fill: var(--ring-gold); }
  .label-center { fill: var(--label-white); }
  .ring-text {
    font-family: "Josefin Sans", sans-serif;
    font-weight: 300;
    font-size: 40px;
    letter-spacing: 20px;
    fill: var(--ring-text);
  }
  .ring-dot { fill: var(--ring-text); }
  .brand-mark { fill: none; stroke: var(--brand-gold); stroke-width: 3; }
  .brand-name {
    font-family: "Cormorant Garamond", serif;
    font-weight: 500;
    font-size: 78px;
    fill: var(--brand-gold);
    letter-spacing: -1px;
  }
  .brand-line {
    font-family: "Cormorant Garamond", serif;
    font-weight: 400;
    font-size: 38px;
    fill: var(--ink-grey);
    letter-spacing: -1px;
  }
  .category {
    font-family: "Montserrat", sans-serif;
    font-size: 22px;
    fill: var(--ink-grey);
  }
  .category-bold { font-weight: 700; }
  .category-light { font-weight: 400; }
  .category-divider { stroke: var(--brand-gold); stroke-width: 2; }
</style>
</head>
<body>
<svg class="label" viewBox="0 0 1200 960" xmlns="http://www.w3.org/2000/svg">
  <defs>
    <path id="arc-top" d="M250,480 A350,350 0 0 1 950,480"/>
    <path id="arc-bottom" d="M220,480 A380,380 0 0 0 980,480"/>
  </defs>

  <circle class="label-edge" cx="600" cy="480" r="420"/>
  <circle class="ring-band" cx="600" cy="480" r="400"/>
  <circle class="label-center" cx="600" cy="480" r="330"/>

  <text class="ring-text">
    <textPath href="#arc-top" startOffset="50%" text-anchor="middle">LEMON &amp; ORANGE OIL</textPath>
  </text>
  <text class="ring-text">
    <textPath href="#arc-bottom" startOffset="50%" text-anchor="middle">LEMON &amp; ORANGE OIL</textPath>
  </text>
  <circle class="ring-dot" cx="235" cy="480" r="7"/>
  <circle class="ring-dot" cx="965" cy="480" r="7"/>

  <circle class="brand-mark" cx="600" cy="320" r="62"/>
  <text class="brand-name" x="600" y="470" text-anchor="middle">SILBERTAU</text>
  <text class="brand-line" x="600" y="522" text-anchor="middle">NATURKOSMETIK</text>

  <text class="category category-bold" x="588" y="590" text-anchor="end">BODY CARE</text>
  <line class="category-divider" x1="606" y1="562" x2="598" y2="604"/>
  <text class="category category-light" x="614" y="590">ORGANIC</text>
</svg>
</body>
</html>
```